BH Marketing Piece

Birch Harbor was created in 1984 as a shared aircraft ownership comprised of individual stockholders, interested in sharing the cost of aircraft ownership. Our strategy is simple, make owning and flying well maintained and upgraded aircraft more affordable through shared ownership.

When you own an aircraft individually, you have all the costs of a loan, hangar, insurance, subscriptions, annual inspection, and those unscheduled maintenance issues.

When you rent an aircraft from a local FBO, you get well used, dirty aircraft that everyone abuses with minimum hour requirements for weekend getaways that turn a 2 hour trip into a 9 hour hit on your wallet.

The solution? Shared aircraft ownership. Birch Harbor has three aircraft based out of Norvale Regional (KQTN). When you join a partnership, you split fixed costs between multiple individuals, AND get access to multiple well maintained and upgraded aircraft. When you fly, you pay the variable costs of your flight time only. Dividing the fixed expenses among multiple members makes flying much more affordable.

Benefits of shared aircraft ownership:

• Much cheaper than owning an aircraft individually
• Access to multiple aircraft
• Higher quality aircraft than your local FBO

• Hangared aircraft, flown by owners, not renters
• No overnight minimums
• On-line scheduling

www.birchharborflyers.example

```html
<!DOCTYPE html>
<html lang="en">
<head>
<meta charset="utf-8">
<title>Birch Harbor – Shared Aircraft Ownership Mailer</title>
<link rel="stylesheet" href="https://fonts.googleapis.com/css2?family=Roboto+Condensed:wght@300;400;700&family=Arimo:wght@400&family=Tinos:wght@400&display=swap">
<style>
  :root {
    --page: #ffffff;
    --field: #2175a9;
    --white: #ffffff;
    --ink: #111111;
    --postage-ink: #2a2a2a;
    --teal: #6fdfd7;
    --banner-top: #8ccbf0;
    --banner-bottom: #4fa2d8;
    --tow-line: #1f3f73;
    --plane-light: #eef1f4;
    --plane-mid: #c9d0d8;
  }
  * { margin: 0; padding: 0; box-sizing: border-box; }
  html, body {
    width: 1200px;
    height: 930px;
    overflow: hidden;
    background: var(--page);
  }
  .mailer {
    position: relative;
    width: 1200px;
    height: 930px;
    background: var(--page);
  }
  .mailer-face {
    position: absolute;
    left: 30px;
    top: 25px;
    width: 1140px;
    height: 875px;
    background: var(--field);
  }
  .brand {
    position: absolute;
    left: 55px;
    top: 55px;
    color: var(--white);
    font-family: "Roboto Condensed", Arial, sans-serif;
  }
  .brand-name {
    font-weight: 700;
    font-size: 34px;
    line-height: 38px;
    text-transform: uppercase;
    letter-spacing: 1px;
    width: 200px;
  }
  .brand-phone {
    margin-top: 8px;
    margin-left: 5px;
    font-weight: 700;
    font-size: 24px;
    line-height: 28px;
    letter-spacing: 0.3px;
  }
  .postage-area {
    position: absolute;
    left: 960px;
    top: 124px;
    width: 160px;
    text-align: center;
    font-family: "Arimo", Arial, sans-serif;
    font-size: 30px;
    line-height: 42px;
    color: var(--postage-ink);
  }
  .tow-scene {
    position: absolute;
    left: 40px;
    top: 295px;
    width: 1130px;
    height: 200px;
  }
  .banner-text {
    position: absolute;
    left: 62px;
    top: 413px;
    font-family: "Roboto Condensed", Arial, sans-serif;
    font-weight: 700;
    font-size: 26px;
    color: var(--white);
    letter-spacing: 0.3px;
    transform: rotate(1deg);
    transform-origin: left center;
  }
  .address-slot {
    position: absolute;
    left: 636px;
    top: 588px;
    font-family: "Tinos", "Times New Roman", serif;
    font-size: 37px;
    color: var(--ink);
  }
  .headline {
    position: absolute;
    left: 58px;
    top: 752px;
    font-family: "Roboto Condensed", Arial, sans-serif;
    text-transform: uppercase;
    font-size: 52px;
    line-height: 60px;
  }
  .headline-main { display: block; font-weight: 700; color: var(--white); }
  .headline-sub { display: block; font-weight: 300; color: var(--teal); }
</style>
</head>
<body>
<main class="mailer">
  <div class="mailer-face"></div>

  <header class="brand">
    <div class="brand-name">Birch Harbor</div>
    <div class="brand-phone">727-555-0139</div>
  </header>

  <div class="postage-area">Postage<br>Area</div>

  <svg class="tow-scene" viewBox="0 0 1130 200" width="1130" height="200">
    <defs>
      <linearGradient id="bannerFill" x1="0" y1="0" x2="0" y2="1">
        <stop offset="0" stop-color="var(--banner-top)"/>
        <stop offset="1" stop-color="var(--banner-bottom)"/>
      </linearGradient>
      <linearGradient id="planeFill" x1="0" y1="0" x2="0" y2="1">
        <stop offset="0" stop-color="var(--plane-light)"/>
        <stop offset="1" stop-color="var(--plane-mid)"/>
      </linearGradient>
    </defs>
    <path d="M6 88 Q260 84 506 92 L520 184 Q260 186 8 186 Z" fill="url(#bannerFill)"/>
    <line x1="506" y1="92" x2="586" y2="116" stroke="var(--tow-line)" stroke-width="1.5"/>
    <line x1="520" y1="184" x2="600" y2="144" stroke="var(--tow-line)" stroke-width="1.5"/>
    <rect x="543" y="8" width="582" height="187" rx="60" fill="url(#planeFill)" opacity="0.85"
          role="img" aria-label="Photo of a white single-engine high-wing aircraft in flight, towing the banner"/>
  </svg>
  <div class="banner-text">THE ONLY WAY TO OWN AN AIRCRAFT!</div>

  <div class="address-slot">Address may be pasted here</div>

  <h1 class="headline">
    <span class="headline-main">Shared Aircraft</span>
    <span class="headline-sub">Ownership</span>
  </h1>
</main>
</body>
</html>
```